New and upgraded www.valdmorefunds.com content & design financial markets

We need an upgrade of our site. The current site is www.valdmorefunds.com
Navigation with full site map i.e. the user can select any page from any menu item.

The “Insights” (Insikter) page will remain as is except new design AND with far more possibilities to add thumbnails, picts, videos etc. The user will have to logon to be able to read the full story.

The “Produkter & Tjänster” (“How to invest” in current web) will contain about the same info as the current “How to invest” pages.

Some pages will contain one or more videos and or speaker supported “live” graphics which we will supply. The media content shall be easy to change.

The site will have two languages from start, English and Swedish. There will be more languages added within 1 year or slightly more.

All texts will be provided by us.

I’m attaching a PDF with suggested content for some of the new pages. However this is just content and absolutely no design. We need new design for the total of the site as well as for the graphics.

Expectation info:
These sites (Both major players in our business) can be used as inspiration:
https://www.tarvenholm.com/eu/en/
https://www.brightwellpartners.com/index.html

Below some opt-OUT and opt-IN graphic rules in connection with the Web supporting our business acumen and brand:

Opt-OUT:
- images similar to educational comic books - it signals an authoritarian approach where the customer is small (insubstantial).
- images that signal trading, cyber, mystery and fast-paced business. We are extremely long-term and invest in real companies
- avoid images containing coins, calculators and banknotes. We're not a savings bank company. or payment service-branch
- avoid images of large data flows, because we should not make facts complex, but simple and comprehensible
- avoid sensing pictures of photo models. We are real people who stand for our efforts. We're not going to hide.
- avoid pictures of suits and tie. They signal rigid-banking. We're smart-investment, flexible, adaptable. Rather curl up your sleeves and show that we’re building something valuable.
- avoid pictures of skyscrapers and cool bank pictures - because they signal the more old valuations of big capital and giant banks - that we are not at all. I know we've had clean facades before. As long as we're not talking about bank skyscrapers, I'm in.

Opt-IN
- pictures of Lukas in moderate amount - he is our symbol person
- films with Lukas and explaining graphical films - explaining and clarifying
- images of pedagogy that give the customer a sense of overview and insights that we give to the customers in our service
- illustrations that explain and deepen our work
- pictures and bars that in 3d illustrate our consistent results and stable delivery
- images that signal that we have a full grasp of data, flows and analyses - without the image becoming a space adventure
- use the logo as a grid, shape and colour.
- no genre portraits, rather pictures of real customers - which gives a sense of why they are customers here
- images that support our core i.e. is science, innovation, unrestricted thinking (“out of the box” – (don’t like that sentence)), smart-solutions, data-driven, client-cantered, flexible and adaptable to client needs and expectation.
- Solid - to be trustworthy in any economic climate
- Long term - consistent work and choices. No trading. Numbers talk
- Data-driven - real tech - combining years of work in finance with straight on tech

Presenting on the webpage:
The story in text and illustration
Show the truth - we have a great history to show and give space
Only numbers and graphs that has a meaning - no artificial numbers etc.
Updates

Target Market(s)

Europe

Coding

Coded - Design and coding required

Number of Pages Required

5+ page

Colors

Designer to choose colors to be used in the design.

Requirements
Must have
• Colours in line with www.valdmorefunds.com

```html
<!DOCTYPE html>
<html lang="en">
<head>
<meta charset="utf-8">
<title>Valdmore Funds – Your Personal Investment Advisor</title>
<link href="https://fonts.googleapis.com/css2?family=Arimo:wght@400;700&display=swap" rel="stylesheet">
<style>
:root{
  --blue:#1b47ae;
  --blue-mid:#2a52a0;
  --navy:#0b1d66;
  --pale:#d2dcef;
  --ink:#1a1a1a;
  --text:#444;
  --white:#fff;
}
*{margin:0;padding:0;box-sizing:border-box}
html,body{width:1200px;height:4858px;overflow:hidden}
body{font-family:"Arimo",Arial,sans-serif;color:var(--ink);background:var(--white);position:relative}
.abs{position:absolute}
.topbar{top:0;left:0;width:1200px;height:30px;background:var(--blue);color:var(--white);font-size:15px}
.topbar .addr{left:90px;top:7px}
.topbar .phone{right:90px;top:4px;font-size:20px;font-weight:700}
.nav{top:30px;left:0;width:1200px;height:80px;background:var(--white)}
.brand{left:90px;top:24px;display:flex;align-items:center;gap:10px;color:var(--blue);font-size:30px}
.brand i{display:block;width:24px;height:24px;background:var(--blue)}
.menu{right:90px;top:36px;display:flex;gap:20px;font-size:14px;font-weight:700}
.menu span.active{color:var(--blue);border-bottom:2px solid var(--blue)}
.hero{top:110px;left:0;width:1200px;height:582px;background:linear-gradient(135deg,#1a3d78 0%,#4d78b4 45%,#1e3f7c 100%);text-align:center;color:var(--white)}
.hero h1{position:absolute;top:185px;width:100%;font-size:54px;font-weight:700}
.hero p{position:absolute;top:260px;width:100%;font-size:28px}
.btn{display:inline-block;background:var(--blue);color:var(--white);font-weight:700;text-align:center;border-radius:3px}
.hero .btn{position:absolute;left:504px;top:322px;width:198px;height:62px;line-height:62px;font-size:23px}
.welcome .eyebrow{left:90px;top:785px;color:var(--blue);font-size:17px}
.welcome h2{left:90px;top:812px;font-size:38px;line-height:48px;font-weight:700}
.welcome p{left:90px;top:925px;width:398px;border-left:2px solid var(--blue);padding-left:14px;font-size:12.5px;line-height:27px;color:var(--text);text-align:justify}
.btn-sm{width:150px;height:47px;line-height:47px;font-size:14px}
.frame{background:var(--blue)}
.photo{display:block}
.trio{top:1198px;left:0;width:1200px;height:285px;display:flex;color:var(--white)}
.trio .card{flex:1;padding:62px 0 0 90px;position:relative}
.trio .card:nth-child(1){background:var(--blue)}
.trio .card:nth-child(2){background:var(--blue-mid);padding-left:38px}
.trio .card:nth-child(3){background:var(--navy);padding-left:38px}
.trio h3{font-size:22px;font-weight:700;display:flex;align-items:center;gap:10px}
.trio h3 b{font-size:27px}
.trio h3 em{display:inline-block;width:44px;height:1px;background:var(--white)}
.trio p{margin-top:22px;font-size:15px;line-height:27px;width:290px}
.trio a{position:absolute;bottom:52px;font-size:12px;font-style:italic;text-decoration:underline}
.approach h2{top:1565px;width:1200px;text-align:center;color:var(--blue);font-size:38px;font-weight:700}
.approach .lead{top:1637px;left:200px;width:800px;text-align:center;font-size:21px;line-height:33px;color:var(--text)}
.feature{width:320px;text-align:center}
.feature .ic{width:104px;height:104px;border-radius:50%;background:var(--blue);margin:0 auto;display:flex;align-items:center;justify-content:center}
.feature .ic.out{background:var(--white);border:3px solid var(--blue)}
.feature h4{margin-top:15px;color:var(--blue);font-size:21px;line-height:27px;font-weight:700}
.feature p{margin-top:38px;font-size:17px;line-height:27px;color:var(--text)}
.band{left:0;width:1200px;background:var(--pale)}
.sec-h{color:var(--blue);font-size:36px;line-height:43px;font-weight:700}
.ticks{list-style:none;font-size:15px}
.ticks li{height:45px;display:flex;gap:16px;align-items:flex-start}
.ticks li::before{content:"»";color:var(--blue);font-size:22px;line-height:16px}
.body-txt{font-size:15.5px;line-height:34px;color:var(--ink);text-align:justify}
.footer{top:4397px;left:0;width:1200px;height:461px;background:var(--blue);color:var(--white)}
.footer h5{font-size:26px;font-weight:700;position:absolute;top:66px}
.footer .col1{left:90px}.footer .col2{left:419px}.footer .col3{left:675px}
.fitem{position:absolute;display:flex;gap:14px;font-size:15px;line-height:22px}
.links{position:absolute;top:120px;left:419px;font-size:14px;line-height:30.5px}
.field{position:absolute;height:44px;border:1px solid rgba(255,255,255,.7);font-size:11px;padding:16px 0 0 15px}
.submit{position:absolute;left:675px;top:288px;width:191px;height:42px;border:1px solid var(--white);border-radius:4px;text-align:center;line-height:40px;font-weight:700;font-size:16px}
.social{position:absolute;top:360px;left:98px;display:flex;gap:6px}
.social span{width:34px;height:34px;border:2px solid var(--white);border-radius:50%}
.copy{position:absolute;top:411px;left:0;width:1200px;border-top:1px solid rgba(255,255,255,.35);text-align:center;padding-top:16px;font-size:15px}
</style>
</head>
<body>

<div class="abs topbar">
  <span class="abs addr">&#9679; 14 Rue des Tilleuls L-2210 Luxembourg</span>
  <span class="abs phone">&#9742; +352 4410 2290</span>
</div>

<header class="abs nav">
  <div class="abs brand"><i></i>Valdmore Funds</div>
  <nav class="abs menu">
    <span class="active">Home</span><span>Products &amp; Services</span><span>Fund Results</span><span>Method Insights</span><span>Questions &amp; Answers</span><span>Contact Valdmore</span>
  </nav>
</header>

<section class="abs hero" role="img" aria-label="Glass office building seen from below under a blue sky">
  <h1>Your Personal Investment Advisor</h1>
  <p>Valdmore Funds is Your Global Reference for Investment Advice</p>
  <span class="btn">GET STARTED</span>
</section>

<section class="welcome">
  <div class="abs eyebrow">WELCOME THERE!</div>
  <h2 class="abs">Welcome To<br>The Valdmore Funds</h2>
  <p class="abs">We are a privately held firm dedicated to clients who have entrusted us with their wealth. We act solely and transparently in the best interest of our clients. We pride ourselves on our discretion and confidentiality.</p>
  <span class="abs btn btn-sm" style="left:90px;top:1053px">MORE ABOUT US</span>
  <div class="abs frame" style="left:708px;top:802px;width:385px;height:313px"></div>
  <div class="abs photo" style="left:721px;top:787px;width:389px;height:313px;background:linear-gradient(135deg,#3a4654,#8c98a6 55%,#cfd6de)" role="img" aria-label="Hands reviewing printed charts on a desk"></div>
  <div class="abs" style="left:890px;top:922px;width:48px;height:44px;background:var(--blue)">
    <svg width="48" height="44" viewBox="0 0 48 44"><circle cx="23" cy="20" r="9" fill="none" stroke="#fff" stroke-width="2"/><path d="M29 26l6 6M23 16v8M19 20h8" stroke="#fff" stroke-width="2"/></svg>
  </div>
</section>

<section class="abs trio">
  <div class="card"><h3><b>01</b><em></em>Why Choose Us</h3><p>We secure your interests by continuously keeping your Investment optimal</p><a style="left:82px">VIEW MORE</a></div>
  <div class="card"><h3><b>02</b><em></em>Investment Intelligence</h3><p>Tailor-made Solutions to Preserve and Grow Wealth in All Market Conditions.</p><a style="left:28px">VIEW MORE</a></div>
  <div class="card"><h3><b>03</b><em></em>Client Focus</h3><p>We are dedicated to offer you exceptional service and unbiased financial advice.</p><a style="left:30px">VIEW MORE</a></div>
</section>

<section class="approach">
  <h2 class="abs">Our Approach</h2>
  <p class="abs lead">Valdmore Funds is truly different – We deliver Investment Services that sets us apart from our contemporaries</p>
  <div class="abs feature" style="left:72px;top:1731px">
    <div class="ic"><svg width="54" height="54" viewBox="0 0 54 54" fill="none" stroke="#fff" stroke-width="2"><path d="M6 6v42h42"/><path d="M14 36l10-12 8 6 12-16"/><circle cx="24" cy="24" r="3"/><circle cx="32" cy="30" r="3"/></svg></div>
    <h4>Valdmore Investment<br>Management System ®</h4>
    <p>Built on a combination of macroeconomic and fundamental analysis</p>
  </div>
  <div class="abs feature" style="left:430px;top:1731px">
    <div class="ic out"><svg width="58" height="54" viewBox="0 0 58 54" fill="none" stroke="#1b47ae" stroke-width="2.5"><path d="M22 44V30M30 44V24M38 44V18M46 44V12M6 48h48"/><path d="M20 20l10-8 8 4 12-10"/><circle cx="14" cy="40" r="7" fill="#1b47ae"/></svg></div>
    <h4>VIQS ® Investment<br>Generator</h4>
    <p>Valdmore iQ Software VIQS® is designed to analyse, forcast, generate and monitor an infinite number</p>
  </div>
  <div class="abs feature" style="left:798px;top:1731px">
    <div class="ic"><svg width="54" height="54" viewBox="0 0 54 54" fill="none" stroke="#fff" stroke-width="2"><rect x="10" y="8" width="24" height="32"/><path d="M15 16h14M15 22h14M15 28h8"/><circle cx="38" cy="38" r="9"/></svg></div>
    <h4>Our<br>Services</h4>
    <p>VIMS® &amp; VIQS® enable Valdmore Funds to deliver customized services &amp; solutions to low cost &amp; risks</p>
  </div>
</section>

<section class="abs band" style="top:2113px;height:542px">
  <div class="abs frame" style="left:89px;top:104px;width:426px;height:368px"></div>
  <div class="abs photo" style="left:102px;top:117px;width:443px;height:370px;background:linear-gradient(135deg,#e9eef4,#9fb3cc 60%,#3c5f96)" role="img" aria-label="Hands pointing a pen at a printed financial chart"></div>
  <h2 class="abs sec-h" style="left:615px;top:86px">Valdmore Investment<br>Advisory Philosophy</h2>
  <ul class="abs ticks" style="left:615px;top:206px">
    <li>Systematic Adaption to Market Climate</li>
    <li>Attractive Risk Returns with Low Portfolio Turnover</li>
    <li>Europe and U.S. Investment Area</li>
    <li>Built to Follow or Outperform the Market During Upturns and</li>
    <li>Avoid Large Declines During Long – Term Market Turndowns</li>
  </ul>
  <span class="abs btn btn-sm" style="left:615px;top:438px;width:145px">READ MORE</span>
</section>

<section>
  <h2 class="abs sec-h" style="left:92px;top:2745px">Valdmore Funds Investment<br>Strategy</h2>
  <ul class="abs ticks" style="left:92px;top:2860px">
    <li>Excellent Historic Performance</li>
    <li>Active Management</li>
    <li>Attractive Risk Returns with Low Portfolio Turnover</li>
    <li>Risk Control</li>
    <li>Low Portfolio Turnover</li>
  </ul>
  <span class="abs btn btn-sm" style="left:92px;top:3098px;width:146px">READ MORE</span>
  <div class="abs frame" style="left:655px;top:2765px;width:426px;height:369px"></div>
  <div class="abs photo" style="left:666px;top:2776px;width:444px;height:370px;background:linear-gradient(135deg,#0d1a2e,#2c4d78 55%,#6c8aa8)" role="img" aria-label="Person holding a tablet showing market charts"></div>
</section>

<section class="abs band" style="top:3242px;height:541px">
  <div class="abs frame" style="left:89px;top:96px;width:426px;height:368px"></div>
  <div class="abs photo" style="left:102px;top:109px;width:443px;height:370px;background:linear-gradient(135deg,#1a1f26,#4a5562 55%,#c9ced4)" role="img" aria-label="Person working at screens displaying financial charts"></div>
  <h2 class="abs sec-h" style="left:609px;top:82px">Investment Intelligence</h2>
  <p class="abs body-txt" style="left:609px;top:139px;width:482px">Your Exclusive Access to European and American Markets and to Our Innovative Investment Approach.We attempt to design attractive long-term return portfolios, with low portfolio turnover, to better withstand fluctuating markets. Our investment process, VIMS, is built to re-allocate to low risk investments during long-term market declines and to follow or outperform the market during upturns. Importantly, we understand that investing shouldn't cause you to lose any sleep.</p>
  <span class="abs btn btn-sm" style="left:609px;top:432px;width:145px">READ MORE</span>
</section>

<section>
  <h2 class="abs sec-h" style="left:90px;top:3874px">Client Focus</h2>
  <p class="abs body-txt" style="left:89px;top:3945px;width:514px;line-height:42px"><em>For Years Financial Institutions Have Said: "Client in the Center"...</em><br>...but they have mainly offered standard solutions without much flexibility leaving the client with a feeling that he is just a number in another box. For us, a client is a real human being who has intentions and ambitions for his portfolio.With current technology, it is not needed to put people in boxes unless you want.</p>
  <span class="abs btn btn-sm" style="left:90px;top:4231px;width:145px">READ MORE</span>
  <div class="abs frame" style="left:655px;top:3878px;width:426px;height:369px"></div>
  <div class="abs photo" style="left:666px;top:3889px;width:444px;height:370px;background:linear-gradient(135deg,#5a4a3c,#8a8f96 50%,#2d3a4e)" role="img" aria-label="Advisor and client in conversation at an office table"></div>
</section>

<footer class="abs footer">
  <h5 class="col1">Contact Us</h5>
  <h5 class="col2">Quick links</h5>
  <h5 class="col3">Request A Quote</h5>
  <div class="fitem" style="left:90px;top:118px"><svg width="20" height="22" viewBox="0 0 20 22" fill="none" stroke="#fff" stroke-width="1.8"><path d="M10 21s7-7 7-12a7 7 0 0 0-14 0c0 5 7 12 7 12z"/><circle cx="10" cy="9" r="2.5"/></svg><span>14 Rue des Tilleuls L-2210<br>Luxembourg</span></div>
  <div class="fitem" style="left:90px;top:183px"><svg width="20" height="20" viewBox="0 0 20 20" fill="none" stroke="#fff" stroke-width="1.8"><path d="M4 2l4 4-2 3c1 2 3 4 5 5l3-2 4 4-3 3C9 18 2 11 1 5z"/></svg><span>Phone:+352 4410 2290</span></div>
  <div class="fitem" style="left:90px;top:220px"><svg width="20" height="20" viewBox="0 0 20 20" fill="#fff"><rect x="2" y="6" width="16" height="12"/><rect x="5" y="2" width="10" height="5"/></svg><span>Fax: 356 3550 7714</span></div>
  <div class="fitem" style="left:90px;top:258px"><svg width="20" height="16" viewBox="0 0 20 16" fill="none" stroke="#fff" stroke-width="1.8"><rect x="1" y="1" width="18" height="14"/><path d="M1 1l9 8 9-8"/></svg><span>Email:<br>info@ValdmoreFunds.com</span></div>
  <div class="links">Home<br>Investment Intelligence<br>Thinking Beyond<br>What We Do<br>Login<br>Disclaimer<br>Contact Us</div>
  <div class="abs" style="left:673px;top:115px;font-size:13px">Alternatively You Can Fill In The Following Contact Form:</div>
  <div class="field" style="left:675px;top:163px;width:211px">Name</div>
  <div class="field" style="left:894px;top:163px;width:211px">E - Mail</div>
  <div class="field" style="left:675px;top:217px;width:211px">Subject</div>
  <div class="field" style="left:894px;top:217px;width:211px">Message</div>
  <div class="submit">SUBMIT</div>
  <div class="social"><span></span><span></span><span></span><span></span></div>
  <div class="copy">(c) 2019 Valdmore Funds | All Rights Reserved | Terms and Conditions</div>
</footer>

</body>
</html>
```